Business Card for Industrial Distributor

We need a business card design for an industrial distributor. We sell machine parts for the manufacturing and oil industry. We would like the cards to look clean and modern but with a touch of industry.

Our colors are blue/white.

Please feel free to visit our website www.korvelpartsco.com

Target Market(s)

mexican manufacturers in the automobile/aerospace industry

Industry/Entity Type

Industrial

Colors
ffffff
0555a3

```html
<!DOCTYPE html>
<html lang="en">
<head>
<meta charset="utf-8">
<title>Korvel Business Card</title>
<link rel="stylesheet" href="https://fonts.googleapis.com/css2?family=Source+Sans+3:wght@400;600;700&display=swap">
<style>
  :root {
    --backdrop: #e8e8e8;
    --card-white: #ffffff;
    --card-blue: #4a62fb;
    --brand-navy: #26369a;
    --brand-sphere: #2447c8;
    --text-light: #ffffff;
    --vertical-name: #eef0fb;
    --faint-arc: rgba(255, 255, 255, 0.14);
  }
  * { margin: 0; padding: 0; box-sizing: border-box; }
  html, body {
    width: 1200px; height: 900px; overflow: hidden;
    background: var(--backdrop);
    font-family: "Source Sans 3", sans-serif;
  }
  .stage { position: relative; width: 1200px; height: 900px; }

  .card {
    position: absolute; width: 347px; height: 560px; overflow: hidden;
    box-shadow: 0 1px 3px rgba(0,0,0,0.12);
  }
  .card-front { left: 237px; top: 171px; background: var(--card-blue); }
  .card-back  { left: 649px; top: 169px; background: var(--card-blue); }

  .front-header {
    position: absolute; left: 0; top: 0; width: 100%; height: 189px;
    background: var(--card-white);
  }
  .brand {
    position: absolute; left: 19px; top: 62px;
    display: flex; align-items: center; gap: 10px;
  }
  .brand-dot {
    width: 64px; height: 64px; border-radius: 50%;
    background: var(--brand-sphere);
  }
  .brand-name {
    font-weight: 700; font-size: 60px; line-height: 1;
    color: var(--brand-navy); letter-spacing: 2px;
  }

  .faint-arc {
    position: absolute; left: 200px; top: 215px;
    width: 330px; height: 380px; border-radius: 50%;
    background: var(--faint-arc);
  }

  .holder { position: absolute; left: 33px; top: 252px; color: var(--text-light); }
  .holder-name { font-weight: 600; font-size: 20px; line-height: 24px; }
  .holder-title { font-weight: 400; font-size: 19px; line-height: 22px; }

  .contacts {
    position: absolute; left: 32px; top: 341px; list-style: none;
    color: var(--text-light); font-size: 17px; line-height: 21.5px;
  }
  .contacts li { display: flex; align-items: center; gap: 10px; }
  .contacts svg { width: 13px; height: 13px; fill: var(--text-light); flex: none; }

  .address {
    position: absolute; left: 31px; top: 461px;
    color: var(--text-light); font-size: 17px; line-height: 22px; font-style: normal;
  }

  .back-name {
    position: absolute; left: 173px; top: 228px;
    transform: translate(-50%, -50%) rotate(-90deg);
    transform-origin: center center;
    font-weight: 700; font-size: 90px; line-height: 1;
    letter-spacing: 6px;
    color: var(--vertical-name); white-space: nowrap;
  }
  .back-dot {
    position: absolute; left: 133px; top: 418px;
    width: 80px; height: 80px; border-radius: 50%;
    background: var(--vertical-name);
  }
</style>
</head>
<body>
<main class="stage">
  <section class="card card-front" aria-label="Card front">
    <div class="faint-arc"></div>
    <header class="front-header">
      <div class="brand">
        <span class="brand-dot"></span>
        <span class="brand-name">Korvel</span>
      </div>
    </header>

    <div class="holder">
      <p class="holder-name">Dana Reyes, Ph.D.</p>
      <p class="holder-title">Administrator</p>
    </div>

    <ul class="contacts">
      <li><svg viewBox="0 0 16 16"><path d="M2 6c0-2 3-3 6-3s6 1 6 3v1h-3V6H5v1H2zM4 8h8l2 5H2z"/></svg>312-555-0148</li>
      <li><svg viewBox="0 0 16 16"><path d="M5 1h6a1 1 0 0 1 1 1v12a1 1 0 0 1-1 1H5a1 1 0 0 1-1-1V2a1 1 0 0 1 1-1zm1 2v8h4V3zm2 9.2a.9.9 0 1 0 0 1.8.9.9 0 0 0 0-1.8z"/></svg>312-555-01927</li>
      <li><svg viewBox="0 0 16 16"><path d="M1 4h14v9H1zm1 1 6 4 6-4"/></svg>info@yourname.com</li>
      <li><svg viewBox="0 0 16 16"><circle cx="8" cy="8" r="7"/></svg>www.website.com</li>
    </ul>

    <address class="address">
      240 W. Lake Street Suite 1610<br>
      Chicago, Illinois 60606
    </address>
  </section>

  <section class="card card-back" aria-label="Card back">
    <span class="back-name">Korvel</span>
    <span class="back-dot"></span>
  </section>
</main>
</body>
</html>
```